4D Cradle Glimpse Luxury Ultrasound Billboard

Design a HIGH-END, MODERN billboard for my private prenatal ultrasound studio, 4D Cradle Glimpse, located in Pace, Florida.
This billboard will be viewed by drivers traveling at highway speeds, so it must be extremely clean, simple, and readable within 6 seconds.
About My Business
4D Cradle Glimpse is a private prenatal ultrasound studio specializing in:
Highest technology 4D/HD Ultrasounds
Early Gender Determination
Pregnancy Confirmation
I have been serving families for nearly 10 years and is known for creating a memorable experience, not just an ultrasound appointment.
Design Style
I DO NOT want:
Flowers
Leaves
Swirls
Glitter
Hearts everywhere
Busy backgrounds
Generic maternity stock graphics
I DO want:
Modern
Luxury
Upscale
Clean
Professional
Eye-catching
Premium medical spa feel
Colors
Use colors from my logo:
LOGO Green ( or a deep green)
Black
White
Soft Gold accents
Images:
Incorporate my professional headshot in a clean, modern way, logo, and the ultrasound images
Text
Keep wording minimal.
Primary Headline ( OPEN TO IDEAS) :
EXAMPLES ( WOULD RATHER SOMETHING MORE CATCHY)
" ADVANCED IMAGING. UNFORGETTABLE MOMENTS"
"MEET YOUR BABY BEFORE BIRTH"
Under headline:
4D Ultrasound • Early Gender • Pregnancy Confirmation
Business Name:
4D Cradle Glimpse
Private Prenatal Ultrasound Studio
Phone Number:
850-471-5923
Important
This billboard must be readable in 5–6 seconds from a moving vehicle.
Less text is better.
The phone number and business name must be visible from a distance.
The design should feel like a premium brand that immediately tells expecting parents:
“This is where I go to see my baby.”
Files Provided
Official logo
Headshot
Ultrasound images
Don’t make this look like a medical office billboard.
Make it look like a luxury baby experience billboard. That’s what separates 4D Cradle Glimpse from hospitals, OB offices, and all the new studios popping up around you. The emotional connection is what gets moms to book. ❤️
Billboard Size - 10.6” x 36”

```html
<!DOCTYPE html>
<html lang="en">
<head>
<meta charset="utf-8">
<title>4D Cradle Glimpse Billboard</title>
<link rel="stylesheet" href="https://fonts.googleapis.com/css2?family=Bebas+Neue&family=Montserrat:wght@500&family=Great+Vibes&display=swap">
<style>
  :root {
    --ink: #0b0b0b;
    --white: #ffffff;
    --gold: #c99a3a;
    --gold-light: #f4b944;
    --green: #4f5e57;
    --page: #eeeeee;
  }
  * { margin: 0; padding: 0; box-sizing: border-box; }
  html, body { width: 1200px; height: 1080px; overflow: hidden; background: var(--page); }
  .billboard {
    position: absolute; left: 40px; top: 377px;
    width: 1120px; height: 325px;
    background: var(--ink); overflow: hidden;
    font-family: "Bebas Neue", "Arial Narrow", sans-serif;
    color: var(--white);
  }
  .billboard__bands { position: absolute; inset: 0; }
  .brand-card {
    position: absolute; left: 47px; top: 24px; width: 310px; height: 151px;
    background: var(--white); border: 3px solid var(--green); border-radius: 22px;
    display: flex; flex-direction: column; align-items: center; justify-content: center;
    text-align: center;
  }
  .brand-card__name { font-size: 44px; line-height: 1; color: var(--green); letter-spacing: 1px; white-space: nowrap; }
  .brand-card__rule { width: 270px; height: 1px; background: var(--gold); margin: 14px 0 10px; }
  .brand-card__tagline { font-family: "Montserrat", sans-serif; font-weight: 500; font-size: 12.8px; color: var(--green); letter-spacing: 0.5px; white-space: nowrap; }
  .headline {
    position: absolute; left: 383px; top: 18px;
    font-size: 93px; line-height: 0.88; letter-spacing: 0.5px; font-weight: 400;
    white-space: nowrap;
  }
  .headline__script {
    font-family: "Great Vibes", cursive; font-size: 82px; color: var(--gold-light);
    display: inline-block; margin-left: 12px; transform: translateY(2px);
  }
  .services { position: absolute; left: 45px; top: 198px; list-style: none; }
  .services li {
    font-size: 38px; line-height: 30px; height: 30px;
    border-left: 3px solid var(--gold); padding-left: 13px;
    margin-bottom: 8px; white-space: nowrap;
  }
  .contact {
    position: absolute; left: 389px; top: 216px; height: 86px;
    border-left: 2px solid var(--white); padding-left: 10px;
  }
  .contact__phone { font-size: 54px; line-height: 0.82; white-space: nowrap; }
  .contact__web { font-size: 48px; line-height: 0.86; color: var(--gold-light); margin-top: 6px; white-space: nowrap; }
  .tablet {
    position: absolute; left: 781px; top: 160px; width: 98px; height: 145px;
    background: #151515; border: 2px solid #2a2a2a; border-radius: 8px;
  }
  .tablet__screen {
    position: absolute; left: 6px; top: 26px; right: 6px; height: 93px;
    background: linear-gradient(135deg, #6b2a1f, #b86a55 45%, #3c120c);
  }
  .headshot {
    position: absolute; left: 900px; top: 17px; width: 194px; height: 308px;
    background: linear-gradient(180deg, #c9b08a 0%, #d8c3a2 30%, #2f4a36 70%, #233b2a 100%);
    border-radius: 97px 97px 0 0;
  }
</style>
</head>
<body>
  <section class="billboard">
    <svg class="billboard__bands" viewBox="0 0 1120 325" width="1120" height="325" aria-hidden="true">
      <defs>
        <linearGradient id="band-left" x1="0" y1="0" x2="0" y2="1">
          <stop offset="0" stop-color="#c99a3a"/>
          <stop offset="1" stop-color="#2a2216"/>
        </linearGradient>
        <linearGradient id="band-right" x1="1" y1="0" x2="0" y2="1">
          <stop offset="0" stop-color="#d9a845"/>
          <stop offset="0.6" stop-color="#8c6a2c"/>
          <stop offset="1" stop-color="#2a2216"/>
        </linearGradient>
      </defs>
      <polygon points="0,0 99,0 17,325 0,325" fill="url(#band-left)"/>
      <polygon points="932,0 1120,0 1120,60 1030,325 830,325" fill="url(#band-right)"/>
      <polygon points="1120,60 1120,325 1030,325" fill="#0b0b0b"/>
    </svg>

    <div class="brand-card">
      <div class="brand-card__name">4D Cradle Glimpse</div>
      <div class="brand-card__rule"></div>
      <div class="brand-card__tagline">PRENATAL ULTRASOUND STUDIO</div>
    </div>

    <h1 class="headline">MEET YOUR BABY<br>BEFORE<span class="headline__script">Birth</span></h1>

    <ul class="services">
      <li>4D Ultrasound</li>
      <li>Early Gender</li>
      <li>Pregnancy Confirmation</li>
    </ul>

    <div class="contact">
      <div class="contact__phone">850-471-5923</div>
      <div class="contact__web">4DCRADLEGLIMPSE.COM</div>
    </div>

    <div class="tablet">
      <div class="tablet__screen" role="img" aria-label="4D ultrasound image of twin babies shown on a tablet"></div>
    </div>

    <div class="headshot" role="img" aria-label="Professional headshot of the studio owner holding an ultrasound probe"></div>
  </section>
</body>
</html>
```